wealth management firm, professional group, new model

we have a logo that works but we need a card, white background using our colors...clean look

our tag line if can be used in

The Path From Saving to Owning

```html
<!DOCTYPE html>
<html lang="en">
<head>
<meta charset="utf-8">
<title>Arlen Wealth Partners – Business Card</title>
<link rel="stylesheet" href="https://fonts.googleapis.com/css2?family=Montserrat:wght@400;500;600&display=swap">
<style>
  :root {
    --navy: #2b3f5e;
    --ink: #4a4f57;
    --rule: #7c8aa0;
    --card: #f8f8f6;
    --backdrop: #e6e6e6;
  }
  * { margin: 0; padding: 0; box-sizing: border-box; }
  html, body {
    width: 1200px;
    height: 800px;
    overflow: hidden;
    background: var(--backdrop);
    font-family: "Montserrat", sans-serif;
  }
  .canvas { position: relative; width: 1200px; height: 800px; }

  .card {
    position: absolute;
    left: 330px;
    width: 540px;
    height: 350px;
    background: var(--card);
  }
  .card--front { top: 35px; }
  .card--back  { top: 415px; }

  /* brand block */
  .brand {
    position: absolute;
    left: 0; right: 0;
    text-align: center;
    color: var(--navy);
    font-weight: 500;
  }
  .brand__mark {
    display: block;
    margin: 0 auto;
    border-radius: 50%;
    background: var(--navy);
  }
  .brand__name { display: block; text-transform: uppercase; }
  .brand__sub  { display: block; text-transform: uppercase; }

  .card--front .brand { left: 265px; width: 220px; right: auto; top: 46px; }
  .card--front .brand__mark { width: 18px; height: 18px; margin-bottom: 12px; }
  .card--front .brand__name { font-size: 34px; letter-spacing: 18px; margin-right: -18px; line-height: 1.1; }
  .card--front .brand__sub  { font-size: 12px; letter-spacing: 3px; margin-top: 16px; }

  .card--back .brand { top: 92px; }
  .card--back .brand__mark { width: 26px; height: 26px; margin-bottom: 26px; }
  .card--back .brand__name { font-size: 52px; letter-spacing: 30px; margin-right: -30px; line-height: 1.1; }
  .card--back .brand__sub  { font-size: 17px; letter-spacing: 4px; margin-top: 24px; }

  /* person */
  .person { position: absolute; left: 62px; top: 178px; }
  .person__name {
    color: var(--navy);
    font-weight: 600;
    font-size: 17px;
    letter-spacing: -0.2px;
    text-transform: uppercase;
    line-height: 1.15;
  }
  .person__title { color: var(--ink); font-size: 15px; line-height: 1.2; }

  .divider {
    position: absolute;
    left: 62px;
    top: 230px;
    width: 415px;
    height: 1px;
    background: var(--rule);
  }

  .contact {
    position: absolute;
    left: 62px;
    top: 242px;
    list-style: none;
    color: var(--ink);
    font-size: 13px;
    line-height: 21px;
  }
  .contact__item { display: flex; align-items: center; gap: 5px; }
  .contact__icon { width: 12px; height: 12px; fill: none; stroke: var(--navy); stroke-width: 1.4; }
  .contact__icon--solid { fill: var(--navy); stroke: none; }

  .tagline {
    position: absolute;
    left: 0; right: 0;
    top: 291px;
    text-align: center;
    color: var(--ink);
    font-size: 12.5px;
    letter-spacing: 0.3px;
    text-transform: uppercase;
  }
</style>
</head>
<body>
<main class="canvas">

  <section class="card card--front" aria-label="Card front">
    <div class="brand">
      <span class="brand__mark"></span>
      <span class="brand__name">Arlen</span>
      <span class="brand__sub">Wealth Partners</span>
    </div>

    <div class="person">
      <p class="person__name">Daniel R. Hoyt</p>
      <p class="person__title">Brand Manager</p>
    </div>

    <div class="divider"></div>

    <ul class="contact">
      <li class="contact__item">Via Lentasio 14 20122 Milano, Italy</li>
      <li class="contact__item">
        <svg class="contact__icon contact__icon--solid" viewBox="0 0 24 24" aria-hidden="true">
          <path d="M6.6 10.8a15.1 15.1 0 0 0 6.6 6.6l2.2-2.2a1 1 0 0 1 1-.25 11.4 11.4 0 0 0 3.6.57 1 1 0 0 1 1 1V20a1 1 0 0 1-1 1A17 17 0 0 1 3 4a1 1 0 0 1 1-1h3.5a1 1 0 0 1 1 1c0 1.25.2 2.45.57 3.57a1 1 0 0 1-.25 1z"/>
        </svg>
        +39.340.555.0187
        <svg class="contact__icon" viewBox="0 0 24 24" aria-hidden="true">
          <rect x="2" y="5" width="20" height="14"/>
          <path d="M2 5l10 8 10-8M2 19l7-7M22 19l-7-7"/>
        </svg>
      </li>
      <li class="contact__item">
        <svg class="contact__icon" viewBox="0 0 24 24" aria-hidden="true">
          <circle cx="12" cy="12" r="10"/>
          <path d="M2 12h20M12 2c3 3 3 17 0 20M12 2c-3 3-3 17 0 20M4 7h16M4 17h16"/>
        </svg>
        www.arlenwealth.com
      </li>
    </ul>
  </section>

  <section class="card card--back" aria-label="Card back">
    <div class="brand">
      <span class="brand__mark"></span>
      <span class="brand__name">Arlen</span>
      <span class="brand__sub">Wealth Partners</span>
    </div>
    <p class="tagline">The Path From Saving to Owning</p>
  </section>

</main>
</body>
</html>
```